Business Card for beauty technology startup

Design Glimora Business Card for a Beauty, based on the website identity and colors (https://www.glimora-example.com).
Glimora is a beauty tech startup that gathers helpful product info for beauty lovers and consumers (such as availability on stores, price range and product reviews) for makeup products. The card design must be young, colorful but clean, and very modern.

Target Market(s)

woman, 15-35

Industry/Entity Type

Cosmetics

Contact Information for Business Card

Full Name, address, phone

Font styles to use
Other font styles liked:
• Advent Pro

Colors
e34297
86cfc6
ffffff
5c5c5c
e8e8e8
e667a6
b2b2b2

Requirements
Must have
• One full colored side with a creative design and another with card info
• Use Color palette: #95C5C5 and/or #D38AA5
• Use fonts: Advent Pro
• Use website identity: https://www.glimora-example.com
Nice to have
• If needed extra font: Roboto

```html
<!DOCTYPE html>
<html lang="en">
<head>
<meta charset="utf-8">
<title>Glimora Business Card</title>
<link rel="stylesheet" href="https://fonts.googleapis.com/css2?family=Open+Sans:wght@300;400;700&display=swap">
<style>
  :root {
    --card-pink: #d489a5;
    --ink-white: #ffffff;
    --backdrop: #ececec;
  }
  * { margin: 0; padding: 0; box-sizing: border-box; }
  html, body { width: 1200px; height: 900px; overflow: hidden; }
  body {
    position: relative;
    background: var(--backdrop);
    font-family: "Open Sans", Arial, sans-serif;
    color: var(--ink-white);
  }
  .card {
    position: absolute;
    background: var(--card-pink);
    overflow: hidden;
  }
  .card--info { left: 77px; top: 33px; width: 588px; height: 364px; }
  .card--brand { left: 388px; top: 505px; width: 566px; height: 352px; }

  .person { position: absolute; left: 31px; top: 44px; }
  .person__name { font-size: 18px; font-weight: 700; letter-spacing: 0.2px; line-height: 1.1; }
  .person__role { font-size: 15px; font-weight: 400; line-height: 1.2; }

  .contact { position: absolute; left: 31px; top: 205px; list-style: none; font-size: 15px; }
  .contact li { display: flex; align-items: center; height: 21.5px; white-space: nowrap; }
  .contact svg { width: 11px; height: 11px; margin-right: 9px; fill: var(--ink-white); flex: none; }
  .address { position: absolute; left: 31px; top: 286px; font-size: 15px; line-height: 22px; font-style: normal; }

  .mark-ring {
    position: absolute; left: 248px; top: 4px;
    width: 340px; height: 340px;
    border: 6px solid var(--ink-white); border-radius: 50%;
    display: flex; align-items: center; justify-content: center;
  }
  .mark-ring__name { font-size: 44px; font-weight: 300; letter-spacing: 6px; }

  .brand-lockup {
    position: absolute; left: 92px; top: 130px;
    display: flex; align-items: center;
  }
  .brand-lockup__dot {
    width: 62px; height: 62px; border: 2px solid var(--ink-white); border-radius: 50%;
    margin-right: 28px;
  }
  .brand-lockup__name { font-size: 50px; font-weight: 300; letter-spacing: 6px; line-height: 1; }
  .brand-url {
    position: absolute; left: 0; right: 0; top: 290px;
    text-align: center; font-size: 16px; font-weight: 400;
  }
</style>
</head>
<body>
  <section class="card card--info">
    <div class="person">
      <p class="person__name">DANIEL HART</p>
      <p class="person__role">Managing Director</p>
    </div>
    <ul class="contact">
      <li><svg viewBox="0 0 12 12"><path d="M2.5 0.5 L4.5 3 L3.5 4.5 Q4.5 7 7.5 8.5 L9 7.5 L11.5 9.5 L10 11.5 Q4 11 0.5 2 Z"/></svg>(044)987654321</li>
      <li><svg viewBox="0 0 12 12"><path d="M0 2 H12 V10 H0 Z M1 3 L6 6.5 L11 3 V3.2 L6 7.5 L1 3.2 Z" fill-rule="evenodd"/></svg>info@glimora-example.com</li>
      <li><svg viewBox="0 0 12 12"><path d="M6 0.5 A5.5 5.5 0 1 0 6 11.5 A5.5 5.5 0 1 0 6 0.5 Z M6 1.8 Q3.5 6 6 10.2 Q8.5 6 6 1.8 Z" fill-rule="evenodd"/></svg>www.glimora-example.com</li>
    </ul>
    <address class="address">1234, Address GoesHere,<br>Country name, 12345</address>
    <div class="mark-ring"><span class="mark-ring__name">GLIMORA</span></div>
  </section>

  <section class="card card--brand">
    <div class="brand-lockup">
      <span class="brand-lockup__dot"></span>
      <span class="brand-lockup__name">GLIMORA</span>
    </div>
    <p class="brand-url">www.glimora-example.com</p>
  </section>
</body>
</html>
```